Business Card for Professional Photographer

I'm looking for an eye catching modern clean design that compliments my logo/ website fonts & colours.
I specialise in architecture, corporate & commercial photography so I'm marketing to professional clients rather than portrait / wedding clients.

I would prefer to not have a solid black design.

My logo brand guide is as follows :

Main front font. : Reislust
Main font colour : #fff
Slogan front font : Ubuntu Bold
Monogram front font : Venti Medium
Container colour : #fff

I need print ready files in pdf .png & .eps formats.

Included in the files below are some screen grabs as reference to font & colours etc.

```html
<!DOCTYPE html>
<html lang="en">
<head>
<meta charset="utf-8">
<title>Clear Angle – Business Card</title>
<link rel="stylesheet" href="https://fonts.googleapis.com/css2?family=Montserrat:wght@300;400&family=Ubuntu:wght@400;700&family=Roboto:wght@400&display=swap">
<style>
  :root {
    --backdrop: #2e2e2e;
    --card: #1c1c1e;
    --gold: #c9a24a;
    --gold-light: #e6c878;
    --text-light: #ffffff;
  }
  * { margin: 0; padding: 0; box-sizing: border-box; }
  html, body {
    width: 799px; height: 1200px; overflow: hidden;
    background: var(--backdrop);
  }
  .canvas {
    position: relative; width: 799px; height: 1200px;
  }
  .card {
    position: absolute; left: 100px; width: 600px; height: 343px;
    background: var(--card);
    border-radius: 4px;
    box-shadow: 0 14px 30px rgba(0,0,0,.45);
    overflow: hidden;
  }
  .card--front { top: 130px; }
  .card--back { top: 720px; }

  /* front */
  .brand {
    position: absolute; left: 0; right: 0; top: 128px;
    display: flex; align-items: center; justify-content: center; gap: 16px;
  }
  .brand__square {
    width: 22px; height: 22px; background: var(--gold);
  }
  .brand__name {
    font-family: "Montserrat", sans-serif; font-weight: 300;
    font-size: 34px; letter-spacing: 8px; color: var(--gold);
  }
  .front-url {
    position: absolute; left: 0; right: 0; top: 262px; text-align: center;
    font-family: "Montserrat", sans-serif; font-weight: 400;
    font-size: 14px; letter-spacing: 3px; color: var(--gold);
  }

  /* back */
  .back-mark {
    position: absolute; left: 40px; top: 60px; width: 200px; height: 200px;
    background: linear-gradient(135deg, var(--gold-light), var(--gold));
  }
  .back-brand {
    position: absolute; right: 34px; top: 42px; text-align: right;
  }
  .back-brand__name {
    font-family: "Montserrat", sans-serif; font-weight: 300;
    font-size: 27px; letter-spacing: 6px; color: var(--gold);
  }
  .back-brand__tagline {
    margin-top: 2px;
    font-family: "Ubuntu", sans-serif; font-weight: 700;
    font-size: 10.5px; letter-spacing: 2.4px; color: var(--gold);
  }
  .person {
    position: absolute; right: 34px; top: 152px; text-align: right;
  }
  .person__name {
    font-family: "Ubuntu", sans-serif; font-weight: 700;
    font-size: 19px; color: var(--gold);
  }
  .person__role {
    font-family: "Roboto", sans-serif; font-size: 14px; color: var(--text-light);
  }
  .contacts {
    position: absolute; right: 34px; top: 220px; list-style: none;
  }
  .contacts__item {
    display: flex; align-items: center; justify-content: flex-end; gap: 10px;
    font-family: "Roboto", sans-serif; font-size: 14px; line-height: 22px;
    color: var(--text-light);
  }
  .contacts__icon { width: 13px; height: 13px; fill: var(--gold); }
  .contacts__spacer { width: 13px; }
</style>
</head>
<body>
<main class="canvas">

  <section class="card card--front">
    <div class="brand">
      <span class="brand__square"></span>
      <span class="brand__name">CLEAR ANGLE</span>
    </div>
    <p class="front-url">www.clearangle.com.au</p>
  </section>

  <section class="card card--back">
    <div class="back-mark"></div>

    <div class="back-brand">
      <p class="back-brand__name">CLEAR ANGLE</p>
      <p class="back-brand__tagline">Architecture Corporate commercial</p>
    </div>

    <div class="person">
      <p class="person__name">Reed Harlow</p>
      <p class="person__role">Photographer</p>
    </div>

    <ul class="contacts">
      <li class="contacts__item">0412555018
        <svg class="contacts__icon" viewBox="0 0 16 16"><path d="M3 1h3l1.5 4-2 1.3a9 9 0 0 0 4.2 4.2L11 8.5l4 1.5v3a2 2 0 0 1-2 2A12 12 0 0 1 1 3a2 2 0 0 1 2-2z"/></svg>
      </li>
      <li class="contacts__item">info@clearangle.com.au
        <svg class="contacts__icon" viewBox="0 0 16 16"><path d="M1 3h14v10H1z M1 3l7 6 7-6" fill="none" stroke="#c9a24a" stroke-width="1.6"/></svg>
      </li>
      <li class="contacts__item">www.clearangle.com.au
        <svg class="contacts__icon" viewBox="0 0 16 16"><circle cx="8" cy="8" r="6.5" fill="none" stroke="#c9a24a" stroke-width="1.4"/><path d="M1.5 8h13M8 1.5c-3 3.5-3 9.5 0 13M8 1.5c3 3.5 3 9.5 0 13" fill="none" stroke="#c9a24a" stroke-width="1.2"/></svg>
      </li>
      <li class="contacts__item">48 Harbour Rd Lorne Vic 3232
        <span class="contacts__spacer"></span>
      </li>
    </ul>
  </section>

</main>
</body>
</html>
```